Brochure Brightwell Hearth Partners

Brochure 12 x 9 tri fold with insert/ Rack card 9x4. Brightwell Hearth Partners 318 Corvane Street Easton, MD 21629410-822-2207AgingAtHomeSolution.com Tag: Devoted to Thoughtful Household Support.
What we do: Home care agency that services higher end Clients Artsy area on the water. Taking care of seniors in their home.

Our story: Opening Brightwell Hearth Partners, Inc. is my way of making a difference in an industry that is dominated by franchises that often have their policies dictated by corporate policy-makers who are unfamiliar with local customs. My goal is to raise the level of non-medical home health care in our area by providing additional, customized training, higher wages for our care-partners and an inclusive workforce in the decision-making process when developing customized care planning for our clients. Through collaboration with the client, their family and care-partners I have learned what issues, concerns and disappointments may arise which enables me to provide a more defined solution for those in need.My goal of providing superior training required locating a nationally recognized curriculum that would serve our clients’ needs. I found the perfect fit with Norla Vance’s, Kindred Pathway Method™ and her Shifting Stones Series™. These programs provide our care-partners with the tools needed to handle the challenges of natural aging and living with Dementia. I was so impressed with these programs, I became a Certified Independent Trainer; one of five in the State of Maryland. There is a bonus for our care-partners who are required to maintain Continuing Education Units - these programs qualify for credit! Improving our industry by providing exemplary care-partners is my goal!I look forward to assisting you with your needs! Dana Prewitt Owner

Services: Companion Care Service - Conversation and Companionship , Meal Preparation, Light House Keeping, Errand Service ,Grocery Shopping ,Incidental Transportation, Laundry & Linen Washing, Medication Reminders, Recreational Activities ,
Personal Care Services: Bathing ,Mobility ,Transferring & Positioning ,Incontinence Care ,Oral Hygiene ,Feeding, Toileting ,Grooming & Dressing, Special Diet Preparation.

Our Commitment to You: Extensive Care-Partner Education - We provide, in addition to state mandated training, eight additional hours of hands-on Dementia training from a Certified, Independent Instructor on the “Kindred Pathway Method” by Norla Vance, a nationally recognized instructor on aging.

Nutrition/Local Chef Inspired Training ;We provide six, two-hour food preparation sessions for our care-partners using local chefs, their recipes and locally grown food.

Meaningful & Engaging Activities - We provide a monthly list with local activities to our care-partners based on our client’s interest and capabilities. Focusing on what our client loved to do in the past.

Home Solutions When Needed; We provide management services to help keep our clients in their homes by working with current contractors or locating new ones to properly maintain a safe-living environment.

About owner: Dana Prewitt, owner of Brightwell Hearth Partners, has earned her certification as an Independent Trainer in the Kindred Pathway; Method (KPM) by Norla Vance, a nationally recognized instructor on natural aging and aging with Dementia. Dana is one of five certified independent trainers in the state of Maryland. All staff will have eight hours of hands on Dementia Kindred Pathway Method training.

On the insert 11x 4.25 want the top to be sticking out of the tri -fold "Dementia Experts . I would like to have shades of each STONE as it progresses
The Shifting STONES(R): The STONES model recognizes the dynamic nature of the human brain and its abilities. Unlike other cognitive models, it acknowledges that everyone’s abilities can change in a moment. Modifying environments, situations, interactions, and expectations will create either supportive positive opportunities or result in distress and a sense of failure. Just as gemstones need different settings and care to show their best characteristics, so do people. Rather than focusing on a person’s loss when there is brain change, seeing individuals as precious, unique, and capable encourages a care partnership and is the core of this model. Providing supportive settings for everyone, including care providers, allows them to use what they have to be their best. The STONES® advocate that everyone living with brain change when given the opportunity will shine. Norla Vance and Kindred Pathway Method

Sapphire ~ True Blue ~ Optimal Cognition, Healthy Brain•
True to self: personal preferences remain basically the same
• Can be flexible in thinking and appreciate multiple perspectives
• Stress/pain/fatigue may trigger Diamond state: back to Sapphire with relief
• Able to suppress and filter personal reactions: chooses effective responses
• Selects from options and can make informed decisions
• Processes well and able to successfully transition
• Aging doesn’t change ability: processing slows, more effort/time/practice needed
My brain is healthy - true blue. If I am aging normally or distressed, it may be hard for me to find words. I can describe what I am thinking so you understand. I may talk to myself because I am giving myself cues and prompts. I can learn new things and change habits, but it takes time and effort. Honoring my choices and preferences, when possible, is important. I need more time to make decisions. Give me the details and let me think about it before you need an answer. I am able to remember plans and information but supports are helpful. I may like specific prompts such as notes, calendars, and reminder calls. Health changes in vision, hearing, balance, coordination, depression, anxiety, pain, or medication may impact my behavior, but my cognitive abilities remain the same.

Diamond ~ Clear and Sharp ~ Routines and Rituals Rule
• Displays many facets: behavior and perspective can shift dramatically
• Prefers the familiar and may resist change: challenged by transitions
• More rigid and self-focused; sees wants as needs, when stressed
• Personal likes/dislikes in relationships/space/belongings etc, become more intense
• Reacts to changes in environment; benefits from familiar; functional/forgiving
• Needs repetition and time to absorb new/different information or routines
• Trusted authority figures can help: reacts better when respect is mutual
My overall cognition is clear and sharp. When happy and supported, I am capable and shine in my abilities. When distressed, I can be cutting and rigid and may see help as a threat. I have trouble seeing other points of view and may become less aware of boundaries or more possessive about my relationships, personal space, and belongings. I have many facets so people see me differently depending on the situation. This can cause conflict among my family, friends, or care team as it’s hard to tell if I am choosing my behavior or truly have limits in my ability. I can socially engage and have good cover skills. People will vary in their awareness of what is happening to me. I want to keep habits and environments as they have always been, even if they are problematic for me or others. I am often focused on the past, personal values, or finances. I will need help to make changes in my life; it’s hard for me. I can be in a Diamond state for reasons other than dementia.

Emerald ~ Green and On the Go With a Purpose ~ Naturally Flawed
• Sees self as able and independent, with limited awareness of changes in ability
• Lives in moments of clarity mixed with periods of loss in logic/reason/perspective
• Understanding and use of language change: vague words and many repeats
• Cues and support help when getting to/from places and doing daily routines
• Awareness of time, place, and situation will not always match current reality
• Strong emotional reactions are triggered by fears, desires, or unmet needs
Needs to know what comes next: seeks guidance and assistance to fill the day
I am flawed; it is part of being a natural emerald. I tend to be focused on what I want or need in this moment and may not be aware of my own safety or changing abilities. I can chat socially, but I typically miss one out of every four words and cannot accurately follow the meaning of longer conversations. I won’t remember the details of our time together, but I will remember how your body language and tone of voice made me feel. I may hide or misplace things and believe someone has taken them. My brain will make up information to fill in the blanks, which makes you think I am lying. If you try to correct me or argue, I may become resentful or suspicious of you. I am not always rational, but I don’t want to be made to feel incompetent. My brain plays tricks on me, taking me to different times and places in my life. When I am struggling, I may tell you, “I want to go home.” To provide the help and assistance I need, you must go with my flow, use a positive, partnered approach, and modify my environment.

Amber ~ Caught in a Moment of Time ~ Caution Required
• Focused on sensation: seeks to satisfy desires and tries to avoid what is disliked
•Environment can drive actions and reactions without awareness of safety
• Visual abilities are limited: focus is on pieces or parts, not the whole picture
• What happens to or around an Amber, may cause strong and surprising reactions
• Enters others’ space and crosses boundaries attempting to meet own needs
• Has periods of intense activity: may be very curious or repetitive with objects or actions
• Care is refused or seen as threatening, due to differences in perspective and ability.
Like a particle trapped in an amber, I am caught in a moment of time. It may surprise you to see how I take in the world around me. I may not know you or see you as a whole person. I react to you based on how you look, sound, move, smell, and respond to me. I like to do simple tasks over and over and may need to repeatedly move and touch, smell, taste, take or tear items apart. While it may exhaust or frustrate you, it soothes me. I don’t recognize danger; you will have to safeguard my environment. I’m intolerant to discomfort because my mouth, hands, feet, and genitalia are highly sensitive due to changes in my nervous system. Therefore, activities like eating, taking medication, mouth care, bathing, dressing, and toileting may distress me. Please notice my reaction and stop if I am resisting. I can’t help myself and one or both of us may get hurt emotionally and/or physically. If this happens, wait a few minutes, connect with me, and try a different approach; possibly substituting one area of focus for another.

Ruby ~ Deep and Strong in Color ~ Others Stop Seeing What is Possible
• Makes use of rhythm: can usually sing, hum, pray, sway, rock, clap, and dance
• When moving can’t stop; when stopped can’t get moving: needs guidance and help
• Big, strong movements are possible, while skilled abilities are being lost
• Danger exists due to limited abilities combined with automatic actions or reactions
• Tends to miss subtle hints, but gets magnified facial expressions and voice rhythms
• Can mimic actions or motions, but will struggle to understand instructions/gestures
• Able to pick up and hold objects, and yet not know what to do with them
As the deep red of a ruby masks detail, my obvious losses make my remaining abilities harder to notice. Although my fine motor skills have become very limited, remember that I am able to move and do simple things with my hands. You will need to anticipate, identify, and respond to all of my needs, even though I may not be aware of them. Plan to create a supportive environment, help with the details of care, and structure my day. Just as a crossing guard directs traffic, you will need to guide my movements and transitions. I can rarely stop or start on my own and switching gears is a challenge. Move with me first, then use your body to show me what you want me to do next, going one step at a time. Palm-beneath-Palm™ assistance helps me to feel safe and secure and to know what to do. Danger is part of my life, due to losses in visual skills, chewing abilities, balance, and coordination. You can reduce the risks to me, but not eliminate them. I can still have moments of joy when you are able to provide what gives me pleasure.

Pearl ~ Hidden Within a Shell ~ Beautiful Moments to Behold
• Will frequently recognize familiar touches, voices, faces, aromas, and tastes• Personhood survives, although all other capabilities are minimal
• Understanding input takes time: go slow and simplify for success
• In care, first get connected by offering comfort then use careful and caring touch
• Changes in the body are profound: weight loss, immobility, systems are failing
• As protective reflexes are lost, breathing, swallowing, and moving will be difficult
Care partners benefit from learning the art of letting go rather than simply giving up
While hidden like a pearl in an oyster shell, I will still have moments when I become alert and responsive. I am near the end of my life. Moments of connection create a sense of wholeness and value between us. Use our time together not just to provide care, but to comfort and connect with me. To help me complete life well, it’s important to honor my personhood when making medical or care decisions; please don’t talk about me as though I am not still here. I respond best to familiar voices and gentle rhythmic movements. I am ruled by reflexes and will startle easily. My brain is losing its ability to control and heal my body. Be prepared to see me having difficulty breathing or swallowing. My body may no longer desire food and drink as I prepare to leave this life. I may not be able to stop living without permission from you. Your greatest gift at this time in my life is to let me know that it is okay to go.

Target Market(s)

Children of seniors, seniors , rehabilitation centers

Requirements
Must have
• Nice photos of Seniors that are happy doing thing they like to do with help (Caregivers)
• Upbeat . Positive
Nice to have
• Processional looking - but very personal, we are taking care of their love ones
Should not have
• Not to feel like a cold hospital or end of life

```html
<!DOCTYPE html>
<html lang="en">
<head>
<meta charset="utf-8">
<title>Brightwell Hearth Partners – Tri-fold Brochure</title>
<link href="https://fonts.googleapis.com/css2?family=Open+Sans:wght@400;600;700&family=Montserrat:wght@500;700;800&family=Great+Vibes&display=swap" rel="stylesheet">
<style>
:root{
  --stage:#5b5b5d;
  --paper:#ffffff;
  --blue:#2b8fcb;
  --blue-dark:#1f6fa3;
  --pink:#e2588c;
  --pink-soft:#fbe3ec;
  --gold:#d6c24c;
  --green:#8cb83e;
  --ink:#4a4a4a;
  --label:#e9e9e9;
}
*{box-sizing:border-box;margin:0;padding:0}
html,body{width:1200px;height:2632px;overflow:hidden}
body{background:var(--stage);font-family:"Open Sans",Arial,sans-serif;color:var(--ink);position:relative}
.section-label{position:absolute;left:0;width:1200px;text-align:center;font-family:"Montserrat",Arial,sans-serif;font-weight:500;font-size:26px;letter-spacing:2px;color:var(--label)}
.spread{position:absolute;left:30px;width:1140px;height:826px;background:var(--paper);overflow:hidden;box-shadow:0 6px 18px rgba(0,0,0,.35)}
.panel{position:absolute;top:0;width:380px;height:826px;overflow:hidden}
.panel + .panel{border-left:1px solid #eee}
.photo{position:absolute}
.footer-band{position:absolute;left:0;bottom:0;width:100%;height:34px;background:var(--pink-soft);font-size:10px;color:var(--blue-dark);text-align:center;line-height:34px;font-weight:600}
.brand-name{font-family:"Montserrat",Arial,sans-serif;font-weight:700;color:var(--blue);display:flex;align-items:center;gap:8px}
.brand-name .dot{width:14px;height:14px;border-radius:50%;background:var(--pink);flex:none}
.script{font-family:"Great Vibes",cursive}
.tab{position:absolute;left:0;height:40px;padding:0 28px 0 26px;background:var(--gold);color:#fff;font-family:"Great Vibes",cursive;font-size:30px;line-height:40px;border-radius:0 22px 22px 0}
.service-heading{font-family:"Montserrat",Arial,sans-serif;font-weight:700;font-size:13px;color:var(--blue);letter-spacing:.5px}
.service-heading span{color:var(--pink)}
.service-list{list-style:none;font-size:11px;line-height:18px;margin-top:6px}
.service-list li::before{content:"•";color:var(--pink);margin-right:7px}
.body-text{font-size:10px;line-height:14.6px}
.seal{position:absolute;border-radius:50%;background:#fff;border:6px solid var(--blue)}
.seal::after{content:"";position:absolute;inset:10px;border-radius:50%;background:var(--green);opacity:.85}
.feature-title{font-family:"Montserrat",Arial,sans-serif;font-weight:700;font-size:14px;color:var(--pink);text-align:center}
.feature-title.blue{color:var(--blue)}
</style>
</head>
<body>

<div class="section-label" style="top:375px">BROCHURE OUTSIDE</div>

<section class="spread outside" style="top:445px">
  <!-- Panel 1: services -->
  <div class="panel services" style="left:0">
    <div class="photo" role="img" aria-label="Photo of a smiling caregiver with a senior at home" style="left:0;top:0;width:380px;height:240px;background:linear-gradient(135deg,#cfe3ef,#f1d9c9 55%,#e9eef3)"></div>
    <svg style="position:absolute;left:0;top:200px" width="380" height="70" viewBox="0 0 380 70"><path d="M0 40 Q190 0 380 30 L380 70 L0 70Z" fill="#fff"/><path d="M0 40 Q190 0 380 30" stroke="var(--blue)" stroke-width="5" fill="none"/><path d="M0 48 Q190 12 380 38" stroke="var(--gold)" stroke-width="3" fill="none"/></svg>
    <div class="tab" style="top:270px">Our Services</div>
    <div style="position:absolute;left:28px;top:330px;width:330px">
      <div class="service-heading"><span>COMPANION</span> CARE SERVICE</div>
      <ul class="service-list">
        <li>Conversation &amp; Companionship</li><li>Meal Preparation</li><li>Light House Keeping</li><li>Errand Service</li><li>Grocery Shopping</li><li>Incidental Transportation</li><li>Laundry &amp; Linen Washing</li><li>Medication Reminders</li><li>Recreational Activities</li>
      </ul>
      <div class="service-heading" style="margin-top:16px"><span>PERSONAL</span> CARE SERVICE</div>
      <ul class="service-list">
        <li>Bathing</li><li>Mobility</li><li>Transferring &amp; Positioning</li><li>Incontinence Care</li><li>Oral Hygiene</li><li>Feeding</li><li>Toileting</li><li>Grooming &amp; Dressing</li><li>Special Diet Preparation</li>
      </ul>
    </div>
    <div class="footer-band">BrightwellHearthPartners.example</div>
  </div>

  <!-- Panel 2: about owner & contact -->
  <div class="panel about" style="left:380px">
    <svg style="position:absolute;left:0;top:0" width="380" height="200" viewBox="0 0 380 200"><path d="M0 0 H380 V120 Q190 60 0 150Z" fill="var(--pink-soft)"/><path d="M0 150 Q190 60 380 120" stroke="var(--gold)" stroke-width="5" fill="none"/></svg>
    <div class="seal" role="img" aria-label="Certification seal" style="left:135px;top:20px;width:110px;height:110px"></div>
    <div class="tab" style="top:168px;left:auto;right:0;border-radius:22px 0 0 22px;background:var(--blue);font-size:28px">About Owner</div>
    <p class="body-text" style="position:absolute;left:28px;top:226px;width:324px;font-size:10.5px;line-height:15.5px">Dana Prewitt, owner of Brightwell Hearth Partners, has earned her certification as an Independent Trainer in the Kindred Pathway Method (KPM) by Norla Vance, a nationally recognized instructor on natural aging and aging with Dementia. Dana is one of five certified independent trainers in the state of Maryland. All staff will have eight hours of hands on Dementia Kindred Pathway Method training.</p>
    <div class="brand-name" style="position:absolute;left:40px;top:420px;width:300px;font-size:20px;justify-content:center"><span class="dot"></span>Brightwell Hearth Partners</div>
    <div style="position:absolute;left:110px;top:480px;width:160px;height:38px;border-radius:19px;background:var(--blue);color:#fff;font-family:Montserrat,Arial,sans-serif;font-weight:700;font-size:14px;text-align:center;line-height:38px">GET IN TOUCH</div>
    <div style="position:absolute;left:0;top:540px;width:380px;text-align:center;font-size:12px;line-height:20px">
      318 Corvane Street<br>Easton, MD 21774<br>
      <span style="display:inline-flex;align-items:center;gap:6px;font-weight:700;color:var(--blue-dark);font-size:15px;margin-top:6px"><svg width="14" height="14" viewBox="0 0 24 24"><path d="M6.6 10.8a15 15 0 0 0 6.6 6.6l2.2-2.2a1 1 0 0 1 1-.25 11.4 11.4 0 0 0 3.6.6 1 1 0 0 1 1 1V20a1 1 0 0 1-1 1A17 17 0 0 1 3 4a1 1 0 0 1 1-1h3.5a1 1 0 0 1 1 1c0 1.25.2 2.45.6 3.6a1 1 0 0 1-.25 1z" fill="var(--pink)"/></svg>410-555-0148</span><br>
      BrightwellHearthPartners.example
    </div>
    <div class="footer-band">BrightwellHearthPartners.example</div>
  </div>

  <!-- Panel 3: cover -->
  <div class="panel cover" style="left:760px">
    <div class="brand-name" style="position:absolute;left:30px;top:40px;width:320px;font-size:22px;justify-content:center"><span class="dot"></span>Brightwell Hearth Partners</div>
    <svg style="position:absolute;left:0;top:100px" width="380" height="60" viewBox="0 0 380 60"><path d="M0 50 Q190 0 380 30" stroke="var(--gold)" stroke-width="5" fill="none"/><path d="M0 58 Q190 10 380 40" stroke="var(--blue)" stroke-width="4" fill="none"/></svg>
    <div class="photo" role="img" aria-label="Photo of a smiling senior woman embraced by her caregiver" style="left:0;top:160px;width:380px;height:360px;background:linear-gradient(160deg,#e6eef4,#f3d8c7 50%,#cfe0ea)"></div>
    <svg style="position:absolute;left:0;top:480px" width="380" height="70" viewBox="0 0 380 70"><path d="M0 40 Q190 70 380 10 L380 70 L0 70Z" fill="#fff"/><path d="M0 40 Q190 70 380 10" stroke="var(--pink)" stroke-width="5" fill="none"/></svg>
    <div style="position:absolute;left:0;top:575px;width:380px;text-align:center;font-family:Montserrat,Arial,sans-serif;color:var(--blue)">
      <div style="font-size:22px;font-weight:500;letter-spacing:1px">WELCOME TO</div>
      <div style="font-size:27px;font-weight:800;line-height:32px;margin-top:4px">BRIGHTWELL HEARTH<br>PARTNERS</div>
      <div style="font-family:'Open Sans',Arial,sans-serif;font-size:13px;font-weight:600;color:var(--pink);margin-top:14px">Devoted to Thoughtful<br>Household Support</div>
    </div>
    <div class="footer-band">BrightwellHearthPartners.example</div>
  </div>
</section>

<div class="section-label" style="top:1361px">BROCHURE INSIDE</div>

<section class="spread inside" style="top:1431px">
  <div class="photo" role="img" aria-label="Banner photo of seniors enjoying time outdoors with caregivers" style="left:0;top:0;width:1140px;height:230px;background:linear-gradient(100deg,#c9dcb8,#e8d8bf 40%,#b9d3a4 70%,#d9e6cf)"></div>
  <svg style="position:absolute;left:0;top:190px" width="1140" height="60" viewBox="0 0 1140 60"><path d="M0 30 Q570 -10 1140 30 L1140 60 L0 60Z" fill="#fff"/><path d="M0 30 Q570 -10 1140 30" stroke="var(--gold)" stroke-width="5" fill="none"/></svg>
  <div class="script" style="position:absolute;left:380px;top:30px;width:760px;text-align:center;font-size:54px;color:#fff;text-shadow:0 2px 6px rgba(0,0,0,.35)">Our Commitment to You:</div>
  <div class="seal" role="img" aria-label="Certification seal" style="left:515px;top:110px;width:110px;height:110px"></div>

  <!-- Panel 1: story -->
  <div class="panel story" style="left:0;top:0;background:transparent;border:none">
    <div class="tab" style="top:245px">Our Story</div>
    <p class="body-text" style="position:absolute;left:22px;top:295px;width:340px;font-size:9.2px;line-height:13.1px">Opening Brightwell Hearth Partners, Inc. is my way of making a difference in an industry that is dominated by franchises that often have their policies dictated by corporate policy-makers who are unfamiliar with local customs. My goal is to raise the level of non-medical home health care in our area by providing additional, customized training, higher wages for our care-partners and an inclusive workforce in the decision-making process when developing customized care planning for our clients. Through collaboration with the client, their family and care-partners I have learned what issues, concerns and disappointments may arise which enables me to provide a more defined solution for those in need.<br><br>My goal of providing superior training required locating a nationally recognized curriculum that would serve our clients’ needs. I found the perfect fit with Norla Vance’s, Kindred Pathway Method™ and her Shifting Stones Series™. These programs provide our care-partners with the tools needed to handle the challenges of natural aging and living with Dementia. I was so impressed with these programs, I became a Certified Independent Trainer; one of five in the State of Maryland. There is a bonus for our care-partners who are required to maintain Continuing Education Units – these programs qualify for credit! Improving our industry by providing exemplary care-partners is my goal!<br><br>I look forward to assisting you with your needs!</p>
    <div style="position:absolute;right:30px;top:735px;text-align:right"><div class="script" style="font-size:24px;color:var(--blue-dark)">Dana Prewitt</div><div style="font-size:10px">Owner</div></div>
  </div>

  <!-- Panel 2: education & nutrition -->
  <div class="panel education" style="left:380px;top:0;background:transparent;border:none">
    <div class="feature-title blue" style="position:absolute;left:20px;top:238px;width:340px;font-size:12px">Extensive Care-Partner Education</div>
    <p class="body-text" style="position:absolute;left:24px;top:262px;width:332px;text-align:center">We provide, in addition to state mandated training, eight additional hours of hands-on Dementia training from a Certified, Independent Instructor on the “Kindred Pathway Method” by Norla Vance, a nationally recognized instructor on aging.</p>
    <div style="position:absolute;left:40px;top:355px;width:300px;height:32px;background:var(--green);color:#fff;border-radius:16px;font-family:Montserrat,Arial,sans-serif;font-weight:700;font-size:11.5px;text-align:center;line-height:32px">Nutrition/Local Chef Inspired Training</div>
    <div class="photo" role="img" aria-label="Photo of fresh locally grown vegetables and a chef preparing food" style="left:30px;top:402px;width:320px;height:250px;background:linear-gradient(140deg,#a9c86e,#e8c268 50%,#c5763f)"></div>
    <p class="body-text" style="position:absolute;left:24px;top:668px;width:332px;text-align:center">We provide six, two-hour food preparation sessions for our care-partners using local chefs, their recipes and locally grown food.</p>
    <div class="footer-band">BrightwellHearthPartners.example</div>
  </div>

  <!-- Panel 3: activities & home solutions -->
  <div class="panel activities" style="left:760px;top:0;background:transparent;border:none">
    <div class="feature-title" style="position:absolute;left:20px;top:238px;width:340px;line-height:18px">Meaningful &amp;<br>Engaging Activities</div>
    <p class="body-text" style="position:absolute;left:24px;top:280px;width:332px;text-align:center">We provide a monthly list with local activities to our care-partners based on our client’s interest and capabilities. Focusing on what our client loved to do in the past.</p>
    <div class="photo" role="img" aria-label="Photo of a senior enjoying a favourite activity with a caregiver" style="left:30px;top:352px;width:320px;height:170px;background:linear-gradient(140deg,#d8e4ee,#efd2bd 55%,#bfd7e8)"></div>
    <div class="feature-title" style="position:absolute;left:20px;top:536px;width:340px;line-height:18px;color:var(--gold)">Home Solutions<br>When Needed</div>
    <p class="body-text" style="position:absolute;left:24px;top:578px;width:332px;text-align:center">We provide management services to help keep our clients in their homes by working with current contractors or locating new ones to properly maintain a safe-living environment.</p>
    <div class="photo" role="img" aria-label="Photo of a contractor making repairs in a senior's home" style="left:30px;top:655px;width:320px;height:125px;background:linear-gradient(140deg,#e9d9a8,#d8b76a 55%,#e8e0cc)"></div>
  </div>
</section>

</body>
</html>
```